Realty Group Needs Classy, Contemporary Letterhead Design

We need a letterhead design for a new realty company located in NY, USA. We buy investment properties to rehabilitate and or keep in our rental portfolio.

```html
<!DOCTYPE html>
<html lang="en">
<head>
<meta charset="utf-8">
<title>Meridian Realty Group Letterhead</title>
<link href="https://fonts.googleapis.com/css2?family=Arimo:wght@400;700&display=swap" rel="stylesheet">
<style>
  :root {
    --purple: #4e2a8e;
    --ink: #2b2b2b;
    --muted: #5a5a5a;
    --rule: #8a8a8a;
    --backdrop: #e9e9eb;
    --paper: #ffffff;
    --sign-tone: #e4e2ea;
  }
  * { box-sizing: border-box; margin: 0; padding: 0; }
  html, body {
    width: 1200px; height: 874px; overflow: hidden;
    background: var(--backdrop);
    font-family: "Arimo", Arial, sans-serif;
  }
  .letterhead {
    position: absolute; left: 300px; top: 13px;
    width: 600px; height: 848px;
    background: var(--paper);
    box-shadow: 0 2px 10px rgba(0,0,0,.12);
    color: var(--ink);
  }
  .brand {
    position: absolute; left: 48px; top: 72px;
  }
  .brand-name {
    font-weight: 700; font-size: 38px; letter-spacing: 1px;
    color: var(--purple); line-height: 1;
  }
  .brand-sub {
    font-weight: 700; font-size: 13px; letter-spacing: 1.5px;
    color: var(--purple); margin-top: 6px; padding-left: 70px;
    border-top: 1.5px solid var(--rule); padding-top: 4px; width: 300px;
  }
  .contact {
    position: absolute; left: 372px; top: 54px;
    border-left: 1px solid var(--rule);
    padding-left: 14px;
    font-size: 10.5px; line-height: 1.45; color: var(--muted);
  }
  .contact-row { display: flex; align-items: center; gap: 5px; }
  .contact-row svg { width: 9px; height: 9px; fill: var(--purple); flex: none; }
  .recipient {
    position: absolute; left: 48px; top: 238px;
    font-size: 11.5px; line-height: 1.45;
  }
  .body-copy {
    position: absolute; left: 48px; top: 318px; width: 504px;
    font-size: 11.5px; line-height: 1.55;
  }
  .body-copy p { margin-bottom: 16px; }
  .closing { margin-top: 4px; }
  .signature {
    width: 130px; height: 52px; margin-top: 12px;
    background: linear-gradient(90deg, var(--sign-tone), #f3f2f6);
    border-radius: 3px;
  }
  .footer-band {
    position: absolute; right: 0; bottom: 70px;
    width: 280px; height: 36px;
    background: var(--purple);
    color: #fff; font-size: 12px;
    display: flex; align-items: center; gap: 8px; padding-left: 18px;
  }
  .footer-band svg { width: 12px; height: 12px; }
</style>
</head>
<body>
  <main class="letterhead">
    <header>
      <div class="brand">
        <div class="brand-name">MERIDIAN</div>
        <div class="brand-sub">Realty Group, LLC</div>
      </div>
      <address class="contact" style="font-style:normal">
        <div>48 Harbor Lane, Suite 210,</div>
        <div>Albany, NY, USA</div>
        <div class="contact-row">
          <svg viewBox="0 0 10 10"><path d="M2 0.5l1.6 1.8-0.8 1.2c0.6 1.3 1.5 2.2 2.7 2.8l1.2-0.8 1.8 1.6-1 1.9C4.3 8.8 1.2 5.7 0.5 2z"/></svg>555-014-2210</div>
        <div class="contact-row">
          <svg viewBox="0 0 10 10"><rect x="2.5" y="0.5" width="5" height="3"/><rect x="0.5" y="3.5" width="9" height="4" rx="1"/><rect x="2.5" y="6.5" width="5" height="3"/></svg>555-018-7734</div>
        <div class="contact-row">
          <svg viewBox="0 0 10 10"><path d="M0.5 2h9v6h-9z M0.5 2l4.5 3.5L9.5 2" fill="none" stroke="#4e2a8e" stroke-width="1"/></svg>info@meridianrealtyllc.com</div>
      </address>
    </header>

    <section class="recipient">
      <div>Mr/s</div>
      <div>First Name and Last Name</div>
      <div>Company Name</div>
      <div>Address</div>
    </section>

    <section class="body-copy">
      <p>Lorem Ipsum is simply dummy text of the printing and typesetting industry. Lorem Ipsum has been the industry's standard dummy text ever since the 1500s, when an unknown printer took a galley of type and scrambled it to make a type specimen book. It has survived not only five centuries, but also the leap into electronic typesetting, remaining essentially unchanged. It was popularised in the 1960s with the release of Letraset sheets containing Lorem Ipsum passages.</p>
      <p>The standard chunk of Lorem Ipsum used since the 1500s is reproduced below for those interested. Sections 1.10.32 and 1.10.33 from "de Finibus Bonorum et Malorum" by Cicero are also reproduced in their exact original form, accompanied by English versions from the 1914 translation by H. Rackham. Lorem ipsum dolor sit amet, consectetur adipiscing elit, sed do eiusmod tempor incididunt ut labore et dolore magna aliqua.</p>
      <p>It is a long established fact that a reader will be distracted by the readable content of a page when looking at its layout. The point of using Lorem Ipsum is that it has a more-or-less normal distribution of letters, as opposed to using 'Content here, content here', making it look like readable English. Many desktop publishing packages and web page editors now.</p>
      <div class="closing">Your Sincerely,</div>
      <div class="signature" role="img" aria-label="Handwritten signature"></div>
    </section>

    <footer class="footer-band">
      <svg viewBox="0 0 12 12"><circle cx="6" cy="6" r="5.5" fill="#fff"/><path d="M3 4c1 0 1.5 1 2.5 0.5S6 3 7 3.5M5 8c1-0.5 2 0 3-1" stroke="#4e2a8e" stroke-width="1" fill="none"/></svg>
      <span>www.meridianrealtyllc.com</span>
    </footer>
  </main>
</body>
</html>
```